New web design for a service provider in the medical field

We are looking for a new design for our website. We are a company that repairs and sells medical endoscopes. Our customers include doctors and hospitals. Our current website can be found at https://lumavex.de/en/lumavex-english.
We need a new web design (without programming) for the following 3 pages:
-Startpage https://lumavex.de/en/lumavex-english/
-Used endoscopes https://lumavex.de/en/used-endoscopes/
-Purchase https://lumavex.de/en/purchase/
The design should be modern and stylish.
The blue color of the logo should be reflected on the page, but not too intrusive.
I have uploaded the images from the header. If more images are needed, let me know and I will upload them.

Target Market(s)
Doctors and hospitals

```html
<!DOCTYPE html>
<html lang="en">
<head>
<meta charset="utf-8">
<title>Lumavex – Contact Us</title>
<link rel="stylesheet" href="https://fonts.googleapis.com/css2?family=Outfit:wght@300;400;500;600;700&family=Barlow:wght@400;500;600&display=swap">
<style>
:root{
  --brand:#29a8e0;
  --ink:#1c3147;
  --text:#3a4654;
  --navy:#0a3a74;
  --navy-deep:#082c5c;
  --line:#d9dde2;
  --white:#fff;
}
*{margin:0;padding:0;box-sizing:border-box}
html,body{width:1200px;height:2249px;overflow:hidden;background:var(--white)}
body{position:relative;font-family:"Outfit",sans-serif;color:var(--text)}
.abs{position:absolute}
a{color:inherit;text-decoration:none}

/* top bar */
.topbar{left:0;top:0;width:1200px;height:33px;background:var(--brand);color:var(--white);font-weight:600;font-size:12px;letter-spacing:.2px}
.topbar .follow{left:101px;top:10px}
.social-dot{width:24px;height:24px;border-radius:50%;border:2px solid var(--white);top:5px}
.topbar nav{right:0;top:0;height:33px;display:flex}
.topbar nav a{padding:0 15px;line-height:35px;border-left:1px solid rgba(255,255,255,.35)}
.topbar nav a:first-child{border-left:none}
.topbar nav a:last-child{padding-right:138px}

/* header */
.brand{display:flex;align-items:center;gap:8px;font-weight:600;color:var(--ink)}
.brand .mark{width:14px;height:14px;border-radius:50%;background:var(--brand)}
.header-brand{left:100px;top:80px;font-size:24px}
.contact-chip{display:flex;gap:8px;align-items:center;top:56px}
.chip-icon{width:24px;height:24px;border-radius:50%;background:var(--brand);display:flex;align-items:center;justify-content:center}
.chip-label{font-size:11px;color:var(--brand);line-height:1.2}
.chip-value{font-size:14px;color:var(--ink)}
.lang{left:997px;top:61px;font-size:12px;font-weight:600;color:var(--ink);display:flex;gap:5px;align-items:center}
.flag{width:14px;height:14px;border-radius:50%;background:#c8283a}
.mainnav{left:285px;top:111px;display:flex;gap:30px;font-size:13px;color:var(--ink)}
.mainnav .active{border-bottom:2px solid var(--brand);padding-bottom:5px}

/* hero */
.hero{left:0;top:158px;width:1200px;height:520px;overflow:hidden}
.hero-photo{position:absolute;inset:0;background:linear-gradient(100deg,#ececee 0%,#e5e5e7 40%,#d6d6d8 70%,#cdcdcf 100%)}
.hero-kicker{left:100px;top:294px;font-size:28px;color:var(--brand);font-weight:400}
.hero-title{left:100px;top:322px;font-size:46px;color:var(--ink);font-weight:700;letter-spacing:.5px}

/* intro */
.section-title{left:0;width:1200px;text-align:center;top:740px;font-size:37px;font-weight:700;color:var(--ink)}
.title-rule{left:567px;top:796px;width:72px;height:3px;background:var(--brand)}
.intro{left:176px;width:848px;top:826px;text-align:center;font-size:16.8px;line-height:26px;font-weight:300;color:var(--text)}
.intro p+p{margin-top:11px}

/* info cards */
.card{top:1014px;height:187px;border:2px solid var(--line);text-align:center;font-size:15px;line-height:23px;color:var(--text);background:var(--white)}
.card h3{font-size:18px;font-weight:600;color:var(--ink)}
.card .body{position:absolute;left:0;right:0}
.card-icon{width:66px;height:66px;border-radius:50%;background:var(--brand);display:flex;align-items:center;justify-content:center}
.dots-deco{left:930px;top:1057px;width:173px;height:171px;background:linear-gradient(#e3f2fa,#e3f2fa) right top/38px 100% no-repeat,linear-gradient(#e3f2fa,#e3f2fa) left bottom/100% 26px no-repeat}

/* contact form */
.form-section{left:0;top:1296px;width:1200px;height:588px;background:linear-gradient(160deg,var(--navy) 0%,#0b3d78 55%,var(--navy-deep) 100%)}
.form-title{left:155px;top:1359px;font-size:34px;font-weight:700;color:var(--white)}
.form-rule{left:156px;top:1407px;width:88px;height:3px;background:var(--white)}
.field{border:1.5px solid rgba(255,255,255,.85);color:var(--white);font-family:"Barlow",sans-serif;font-weight:500;font-size:15px;padding-left:21px;display:flex;align-items:center;height:47px;width:294px}
.field.message{align-items:flex-start;padding-top:18px;width:905px;height:113px}
.checkbox{left:153px;top:1700px;width:24px;height:20px;border:1.5px solid rgba(255,255,255,.85)}
.consent{left:189px;top:1698px;width:836px;font-family:"Barlow",sans-serif;font-size:12.2px;line-height:19px;color:var(--white)}
.send{left:154px;top:1755px;width:180px;height:46px;background:var(--brand);color:var(--white);font-size:13px;font-weight:600;display:flex;align-items:center;justify-content:center;gap:4px}

/* footer */
.footer-brand{left:145px;top:1988px;font-size:26px}
.footer-brand .mark{width:18px;height:18px}
.vdiv{top:1915px;width:1px;height:208px;background:#eef0f2}
.footer-col{top:1967px}
.footer-col h4{font-size:16px;font-weight:600;color:var(--ink);border-left:3px solid var(--brand);padding-left:18px;margin-left:-21px;line-height:22px;margin-bottom:11px}
.footer-col ul{list-style:none;font-size:15px;color:var(--ink);font-weight:300}
.footer-col li{line-height:29.5px}
.foot-social{width:30px;height:30px;border-radius:50%;background:var(--ink);top:2000px}
.cert-badge{left:905px;top:2046px;width:117px;height:82px;background:#1b4e9b;border-bottom:12px solid #e88a1a}
.bottom-rule{left:0;top:2181px;width:1200px;height:1px;background:var(--line)}
.copyright{left:0;width:1237px;text-align:center;top:2201px;font-size:13px;color:#7a8590}
</style>
</head>
<body>

<div class="abs topbar">
  <span class="abs follow">FOLLOW US</span>
  <span class="abs social-dot" style="left:188px"></span>
  <span class="abs social-dot" style="left:222px"></span>
  <nav class="abs">
    <a href="#">PICK-UP ORDER</a>
    <a href="#">ABOUT US</a>
    <a href="#">CONTACT US</a>
  </nav>
</div>

<a class="abs brand header-brand" href="https://lumavex.de/en/lumavex-english/"><span class="mark"></span>Lumavex</a>

<div class="abs contact-chip" style="left:622px">
  <span class="chip-icon"><svg width="13" height="10" viewBox="0 0 13 10"><rect x=".5" y=".5" width="12" height="9" rx="1" fill="none" stroke="#fff"/><path d="M1 1l5.5 4.5L12 1" fill="none" stroke="#fff"/></svg></span>
  <div><div class="chip-label">EMAIL US</div><div class="chip-value">info@lumavex.de</div></div>
</div>
<div class="abs contact-chip" style="left:806px">
  <span class="chip-icon"><svg width="12" height="12" viewBox="0 0 24 24"><path fill="#fff" d="M6.6 10.8a15 15 0 006.6 6.6l2.2-2.2c.3-.3.7-.4 1-.2 1.1.4 2.3.6 3.6.6.6 0 1 .4 1 1V20c0 .6-.4 1-1 1A17 17 0 013 4c0-.6.4-1 1-1h3.5c.6 0 1 .4 1 1 0 1.3.2 2.5.6 3.6.1.3 0 .7-.2 1z"/></svg></span>
  <div><div class="chip-label">CALL US NOW</div><div class="chip-value">+49 4151 555 120-0</div></div>
</div>
<div class="abs lang"><span class="flag"></span>ENG
  <svg width="10" height="6" viewBox="0 0 10 6"><path d="M1 1l4 4 4-4" fill="none" stroke="#1c3147" stroke-width="1.5"/></svg></div>

<nav class="abs mainnav">
  <a href="https://lumavex.de/en/lumavex-english/">HOME</a>
  <a href="#">ENDOSOPE REPAIR</a>
  <a href="https://lumavex.de/en/used-endoscopes/">USED ENDOSCOPES</a>
  <a href="#">ENDOSCOPY SYSTEMS</a>
  <a href="#">ENDOSCOPY ACCESSORIES</a>
  <a class="active" href="https://lumavex.de/en/purchase/">PURCHASE</a>
</nav>

<div class="abs hero">
  <div class="hero-photo" role="img" aria-label="Photograph of a black video endoscope processor head with its insertion cable on a light grey surface"></div>
  <svg class="abs" style="left:0;top:400px" width="1200" height="120" viewBox="0 0 1200 120">
    <path d="M0 12 L600 110 L1200 12 L1200 32 L600 118 L0 32Z" fill="var(--brand)"/>
    <path d="M0 32 L600 118 L1200 32 L1200 120 L0 120Z" fill="#fff"/>
  </svg>
</div>
<div class="abs hero-kicker">GET IN TOUCH</div>
<h1 class="abs hero-title">CONTACT US</h1>

<h2 class="abs section-title">CONTACT US, WE WILL HELP YOU!</h2>
<div class="abs title-rule"></div>
<div class="abs intro">
  <p>Good day! We are looking forward for your message! You can get informations on possible or ongoing repairs of your endoscope technology. You can also get an advise on rational inspection intervals and in choosing the right accessories. Use the contact form below or the possibility of contacting us by post, telephone or email!</p>
  <p>We will contact you as soon as possible!</p>
</div>

<div class="abs dots-deco" role="img" aria-label="Light blue dotted decoration"></div>
<div class="abs card" style="left:151px;width:296px">
  <div class="body" style="top:50px"><h3>Lumavex GmbH</h3>Birkenstraße 18<br>21490 Tannhausen<br>Germany</div>
</div>
<div class="abs card" style="left:462px;width:294px">
  <div class="body" style="top:52px"><h3>Contact media</h3>phone:&nbsp; +49 4151 555 120-0<br>Fax: +49 4151 555 120-1<br>Email: info@lumavex.de</div>
</div>
<div class="abs card" style="left:771px;width:294px">
  <div class="body" style="top:56px"><h3>Opening hours</h3>Monday – Friday<br>08:00 – 20:00</div>
</div>
<div class="abs card-icon" style="left:259px;top:981px">
  <svg width="26" height="30" viewBox="0 0 24 28"><path d="M12 1a9 9 0 00-9 9c0 7 9 17 9 17s9-10 9-17a9 9 0 00-9-9z" fill="none" stroke="#fff" stroke-width="2.2"/><circle cx="12" cy="10" r="3.2" fill="#fff"/></svg>
</div>
<div class="abs card-icon" style="left:571px;top:984px">
  <svg width="26" height="26" viewBox="0 0 24 24"><path fill="#fff" d="M6.6 10.8a15 15 0 006.6 6.6l2.2-2.2c.3-.3.7-.4 1-.2 1.1.4 2.3.6 3.6.6.6 0 1 .4 1 1V20c0 .6-.4 1-1 1A17 17 0 013 4c0-.6.4-1 1-1h3.5c.6 0 1 .4 1 1 0 1.3.2 2.5.6 3.6.1.3 0 .7-.2 1z"/></svg>
</div>
<div class="abs card-icon" style="left:875px;top:984px">
  <svg width="32" height="32" viewBox="0 0 32 32"><circle cx="16" cy="16" r="13" fill="none" stroke="#fff" stroke-width="2.4"/><path d="M16 8v8l5 4" fill="none" stroke="#fff" stroke-width="2.4" stroke-linecap="round"/></svg>
</div>

<section class="abs form-section"></section>
<h2 class="abs form-title">CONTACT FORM</h2>
<div class="abs form-rule"></div>

<div class="abs field" style="left:155px;top:1446px">Saluation Select</div>
<div class="abs field" style="left:460px;top:1446px">Co.Dr. Off</div>
<div class="abs field" style="left:763px;top:1446px">Surname</div>
<div class="abs field" style="left:155px;top:1508px">First name</div>
<div class="abs field" style="left:459px;top:1508px">Email address</div>
<div class="abs field" style="left:762px;top:1508px">Telephone</div>
<div class="abs field message" style="left:153px;top:1569px">Message</div>

<div class="abs checkbox"></div>
<p class="abs consent">I have read the privacy policy and accept it. I agree above input will be transmitted to Lumavex GmbH to get in contact with me respectively to process my request and store all needed informations. Neither a transfer to third parties will happen, nor a use for advertising purposes by Lumavex GmbH!</p>
<a class="abs send" href="#">SEND MESSAGE
  <svg width="8" height="11" viewBox="0 0 8 11"><path d="M1.5 1l4.5 4.5L1.5 10" fill="none" stroke="#fff" stroke-width="2"/></svg></a>

<a class="abs brand footer-brand" href="https://lumavex.de/en/lumavex-english"><span class="mark"></span>Lumavex</a>
<div class="abs vdiv" style="left:431px"></div>
<div class="abs vdiv" style="left:671px"></div>
<div class="abs vdiv" style="left:878px"></div>

<div class="abs footer-col" style="left:451px">
  <h4>NAVIGATION</h4>
  <ul><li>Home</li><li>Endoscope Repair</li><li>Used Endoscope</li><li>Endoscopy Systems</li></ul>
</div>
<div class="abs footer-col" style="left:686px">
  <h4>RESOURCES</h4>
  <ul><li>Endoscopy Accesories</li><li>Purchase</li><li>Contact Us</li></ul>
</div>
<div class="abs footer-col" style="left:903px">
  <h4>FOLLOW US</h4>
</div>
<span class="abs foot-social" style="left:903px"></span>
<span class="abs foot-social" style="left:943px"></span>
<div class="abs cert-badge" role="img" aria-label="Quality management certification badge"></div>

<div class="abs bottom-rule"></div>
<p class="abs copyright">© 2022 Lumavex GmbH All Right Reserved</p>

</body>
</html>
```